Dunmore Roofing

Want a professional looking business card

Industry/Entity Type

Business

Contact Information for Business Card

Paul Dunmore ( Owner) paul@dunmoreroofing-example.com, www.dunmoreroofing-example.com, Adress: 4172 Township road 43 Plantagenet,ON K9X4T2

```html
<!DOCTYPE html>
<html lang="en">
<head>
<meta charset="utf-8">
<title>Dunmore Roofing – Business Card</title>
<link href="https://fonts.googleapis.com/css2?family=Montserrat:wght@400;500;700;800&display=swap" rel="stylesheet">
<style>
  :root {
    --bg: #2a2a2c;
    --brand-blue: #1f3f93;
    --brand-blue-deep: #1c2f8f;
    --brand-blue-light: #274aa0;
    --grey: #7b7b7d;
    --ink: #4a4a4c;
    --white: #ffffff;
  }
  * { margin: 0; padding: 0; box-sizing: border-box; }
  html, body {
    width: 1200px; height: 900px; overflow: hidden;
    background: var(--bg);
    font-family: "Montserrat", sans-serif;
  }
  .canvas { position: relative; width: 1200px; height: 900px; }

  .card {
    position: absolute;
    width: 560px; height: 320px;
    border-radius: 26px;
    overflow: hidden;
    box-shadow: 0 18px 40px rgba(0,0,0,.45);
  }

  /* Back card */
  .card-back {
    left: 60px; top: 100px;
    background: linear-gradient(160deg, var(--brand-blue-deep) 0%, var(--brand-blue-light) 100%);
    color: var(--white);
  }
  .back-brand {
    position: absolute; left: 0; right: 0; top: 112px;
    display: flex; align-items: center; justify-content: center; gap: 12px;
  }
  .brand-mark { width: 14px; height: 14px; background: currentColor; flex: none; }
  .brand-name {
    font-weight: 800; font-size: 34px; letter-spacing: 2px; text-transform: uppercase;
  }
  .back-tagline {
    position: absolute; left: 0; right: 0; top: 162px; text-align: center;
    font-weight: 800; font-size: 15px; letter-spacing: 18px; text-transform: uppercase;
    padding-left: 18px;
  }
  .back-web {
    position: absolute; left: 0; right: 0; bottom: 40px; text-align: center;
    font-size: 13px; letter-spacing: .5px;
  }

  /* Front card */
  .card-front {
    left: 580px; top: 480px;
    background: var(--white);
  }
  .name-band {
    position: absolute; left: 0; top: 0; width: 340px; height: 92px;
    background: var(--brand-blue);
    color: var(--white);
    padding: 28px 0 0 36px;
  }
  .person-name { font-weight: 700; font-size: 19px; letter-spacing: .5px; text-transform: uppercase; }
  .person-role { font-weight: 400; font-size: 13px; margin: 4px 0 0 14px; text-transform: uppercase; }

  .front-brand {
    position: absolute; right: 34px; top: 120px;
    color: var(--brand-blue); text-align: center;
  }
  .front-brand .brand-row { display: flex; align-items: center; gap: 10px; justify-content: center; }
  .front-brand .brand-name { font-size: 27px; }
  .front-brand .brand-sub {
    font-weight: 800; font-size: 12px; letter-spacing: 14px; text-transform: uppercase; margin-top: 6px;
    padding-left: 14px;
    color: var(--brand-blue);
  }

  .address {
    position: absolute; left: 60px; top: 150px;
    color: var(--ink); font-size: 13px; line-height: 1.5; font-style: normal;
  }
  .divider { position: absolute; left: 60px; top: 205px; width: 22px; height: 2px; background: var(--brand-blue); }
  .contacts {
    position: absolute; left: 60px; top: 218px; list-style: none;
    color: var(--ink); font-size: 13px; line-height: 1.6;
  }
  .contacts li { display: flex; align-items: center; gap: 10px; }
  .contacts svg { width: 12px; height: 12px; fill: var(--brand-blue); flex: none; }
  .contacts .web { color: var(--brand-blue); }

  .foot-strip { position: absolute; left: 0; bottom: 0; height: 12px; width: 100%; display: flex; }
  .foot-strip .blue { width: 390px; background: var(--brand-blue); }
  .foot-strip .grey { flex: 1; background: var(--grey); }
</style>
</head>
<body>
<main class="canvas">

  <section class="card card-back">
    <div class="back-brand"><span class="brand-mark"></span><span class="brand-name">Dunmore</span></div>
    <div class="back-tagline">Roofing</div>
    <div class="back-web">www.dunmoreroofing-example.com</div>
  </section>

  <section class="card card-front">
    <div class="name-band">
      <div class="person-name">Paul Dunmore</div>
      <div class="person-role">Owner</div>
    </div>

    <div class="front-brand">
      <div class="brand-row"><span class="brand-mark"></span><span class="brand-name">Dunmore</span></div>
      <div class="brand-sub">Roofing</div>
    </div>

    <address class="address">
      4172 Township road 43<br>
      Larkfield, ON K9X4T2
    </address>
    <div class="divider"></div>
    <ul class="contacts">
      <li><svg viewBox="0 0 24 24"><path d="M6.6 10.8a15 15 0 0 0 6.6 6.6l2.2-2.2c.3-.3.7-.4 1-.2 1.1.4 2.3.6 3.6.6.6 0 1 .4 1 1V20c0 .6-.4 1-1 1A17 17 0 0 1 3 4c0-.6.4-1 1-1h3.5c.6 0 1 .4 1 1 0 1.3.2 2.5.6 3.6.1.3 0 .7-.2 1z"/></svg>(000)123-4567</li>
      <li><svg viewBox="0 0 24 24"><path d="M2 5h20v14H2zm2 2v.5l8 5 8-5V7z"/></svg>paul@dunmoreroofing-example.com</li>
      <li><svg viewBox="0 0 24 24"><circle cx="12" cy="12" r="10"/></svg><span class="web">www.dunmoreroofing-example.com</span></li>
    </ul>

    <div class="foot-strip"><span class="blue"></span><span class="grey"></span></div>
  </section>

</main>
</body>
</html>
```